New Business Card Design Project

I need a design for business cards, i am an electrical business called "Corvane Electrical and Communications" i need the cards to be double sided with the company logo on the back (attached) the front needs to say my company name, web site, email address, telephone number, and ABN number and electrical license number. I am open to different arrangements of the information but would like the background to be incorporating something electrical or something that looks smart. open to all additional ideas also.

The company colours are orange and grey see logo attached.

Business Name: Corvane Electrical and Communications
Website: corvaneelectricalandcomms.example.com.au
Email: brent@corvaneelectricalandcomms.example.com.au
Telephone(mobile): 0481209736
ABN: 71208349162
Lic No: 418273D

Target Market(s)

Business entities, Project Managers, Accounts, Clients

Industry/Entity Type

Electrician

Contact Information for Business Card

I need a design for business cards, i am an electrical business called "Corvane Electrical and Communications" i need the cards to be double sided with the company logo on the back (attached) the front needs to say my company name

Font styles to use
Serif
Sans Serif

Colors
f37122
5c5c5c

Requirements
Must have
• Must have the Logo on the back open to different ways of it being on the back but had in mind to keep it central but again open to other options
Nice to have
• A real modern cool background that is eye catching yet contemporary
Should not have
• No backgrounds of a light bulb or plug or anything like that

```html
<!DOCTYPE html>
<html lang="en">
<head>
<meta charset="utf-8">
<title>Corvane Electrical and Communications – Business Card</title>
<link rel="stylesheet" href="https://fonts.googleapis.com/css2?family=Exo+2:wght@300;400;500&display=swap">
<style>
  :root{
    --page:#e9e7e3;
    --card-dark:#4a4a4c;
    --card-mid:#5c5c5c;
    --card-light:#6e6e70;
    --orange:#f3a51f;
    --orange-deep:#f37122;
    --white:#ffffff;
    --ink-light:#e6e6e6;
    --ink-soft:#bfbfbf;
    --ink-grey:#5c5c5c;
  }
  html,body{margin:0;padding:0;overflow:hidden;}
  body{
    width:1200px;height:843px;background:var(--page);
    font-family:"Exo 2",Arial,sans-serif;position:relative;
  }
  .card{
    position:absolute;width:540px;height:309px;border-radius:18px;overflow:hidden;
    background:linear-gradient(160deg,var(--card-light) 0%,var(--card-mid) 45%,var(--card-dark) 100%);
    box-shadow:0 6px 18px rgba(0,0,0,.25);
  }
  .card-back{left:40px;top:267px;}
  .card-front{left:620px;top:267px;}

  /* back side */
  .back-brand{
    position:absolute;left:0;right:0;top:112px;
    display:flex;align-items:center;justify-content:center;gap:12px;
  }
  .brand-dot{width:16px;height:16px;border-radius:50%;background:var(--orange);}
  .back-brand-name{
    color:var(--orange);font-weight:500;font-size:38px;letter-spacing:6px;text-transform:uppercase;
  }
  .back-web{
    position:absolute;left:0;right:0;top:222px;text-align:center;
    color:var(--ink-light);font-weight:300;font-size:12px;letter-spacing:2px;
  }

  /* front side */
  .front-swoosh{position:absolute;inset:0;}
  .person{
    position:absolute;right:26px;top:62px;text-align:right;
  }
  .person-name{color:var(--orange);font-size:22px;font-weight:400;letter-spacing:1px;text-transform:uppercase;}
  .person-role{color:var(--ink-grey);font-size:15px;font-weight:400;letter-spacing:.5px;}
  .front-brand{
    position:absolute;left:38px;top:118px;display:flex;align-items:center;gap:10px;
  }
  .front-brand .brand-dot{width:12px;height:12px;}
  .front-brand-name{
    color:var(--white);font-weight:400;font-size:15px;letter-spacing:2px;line-height:1.15;text-transform:uppercase;
  }
  .contact{
    position:absolute;left:40px;top:180px;margin:0;padding:0;list-style:none;
    color:var(--ink-light);font-weight:300;font-size:13px;
  }
  .contact li{display:flex;align-items:center;gap:8px;height:22px;}
  .contact svg{width:12px;height:12px;flex:none;}
  .registration{
    position:absolute;right:24px;bottom:22px;text-align:right;
    color:var(--ink-soft);font-weight:400;font-size:15px;line-height:1.45;
  }
</style>
</head>
<body>

  <section class="card card-back" aria-label="Card back">
    <div class="back-brand">
      <span class="brand-dot"></span>
      <span class="back-brand-name">Corvane</span>
    </div>
    <div class="back-web">www.corvaneelectricalandcomms.example.com.au</div>
  </section>

  <section class="card card-front" aria-label="Card front">
    <svg class="front-swoosh" viewBox="0 0 540 309" preserveAspectRatio="none" aria-hidden="true">
      <path d="M290 215 C380 205 470 200 540 150 V230 C460 240 380 230 290 215 Z" fill="#3f3f41" opacity=".55"/>
      <path d="M150 0 H540 V205 C470 175 420 160 360 120 C300 80 230 60 150 0 Z" fill="#ffffff"/>
      <path d="M540 205 C470 175 420 160 360 120 C300 80 230 60 150 0 H175 C240 48 310 70 370 108 C430 145 480 168 540 185 Z" fill="#f1f1f1"/>
      <path d="M20 100 C70 50 140 24 215 26 C260 28 300 38 335 54" fill="none" stroke="#f3a51f" stroke-width="5" stroke-linecap="round"/>
    </svg>

    <div class="person">
      <div class="person-name">Daniel Hart</div>
      <div class="person-role">CEO/FOUNDER</div>
    </div>

    <div class="front-brand">
      <span class="brand-dot"></span>
      <span class="front-brand-name">Corvane Electrical<br>and Communications</span>
    </div>

    <ul class="contact">
      <li>
        <svg viewBox="0 0 12 12"><rect x="3" y="0.5" width="6" height="11" rx="1.2" fill="none" stroke="#f3a51f" stroke-width="1.2"/><circle cx="6" cy="9.5" r=".8" fill="#f3a51f"/></svg>
        0481209736
      </li>
      <li>
        <svg viewBox="0 0 12 12"><rect x="0.6" y="2.2" width="10.8" height="7.6" rx="1" fill="none" stroke="#f3a51f" stroke-width="1.2"/><path d="M1 3l5 4 5-4" fill="none" stroke="#f3a51f" stroke-width="1.2"/></svg>
        brent@corvaneelectricalandcomms.example.com.au
      </li>
      <li>
        <svg viewBox="0 0 12 12"><circle cx="6" cy="6" r="5.3" fill="#f3a51f"/><path d="M1 6h10M6 .7c-2.5 3-2.5 7.6 0 10.6M6 .7c2.5 3 2.5 7.6 0 10.6" fill="none" stroke="#5c5c5c" stroke-width=".9"/></svg>
        corvaneelectricalandcomms.example.com.au
      </li>
    </ul>

    <div class="registration">
      <div>ABN: 71208349162</div>
      <div>Lic No: 418273D</div>
    </div>
  </section>

</body>
</html>
```